Looking for a modern, Professional business card design

We have a simple business card, but are looking for a more modern, professional look. A sample of the basic card is attached as well as the logo. We would also like to add that we offer:
Struggling with your finances?
- Learn to become debt free
- Discover the power of cash
- Control your money instead of it controlling you
Let us help you achieve a new level of financial freedom!
Also, we would like to have a "SPECIAL OFFER!: FREE 30 minute consultation"
Financial Planning

```html
<!DOCTYPE html>
<html lang="en">
<head>
<meta charset="utf-8">
<title>Summit Money Coaching – Business Card</title>
<link rel="stylesheet" href="https://fonts.googleapis.com/css2?family=Open+Sans:wght@400;600;700;800&display=swap">
<style>
  :root {
    --bg: #e9e7e2;
    --card: #ffffff;
    --card-shade: #eceeea;
    --green: #4fa82a;
    --green-light: #8cc63f;
    --green-deep: #2f7d1c;
    --ink: #2b2b2b;
    --grey: #5a5a5a;
    --white: #ffffff;
  }
  * { box-sizing: border-box; margin: 0; padding: 0; }
  html, body { width: 1200px; height: 843px; overflow: hidden; }
  body {
    background: var(--bg);
    font-family: "Open Sans", Arial, sans-serif;
    display: flex;
    flex-direction: column;
    align-items: center;
    justify-content: center;
    gap: 30px;
  }
  .card {
    position: relative;
    width: 660px;
    height: 377px;
    border-radius: 22px;
    overflow: hidden;
    background: linear-gradient(160deg, var(--card) 55%, var(--card-shade) 100%);
    box-shadow: 0 10px 26px rgba(0,0,0,0.22);
  }

  /* Back side */
  .brand-decoration {
    position: absolute;
    left: 0; top: 0;
    width: 200px; height: 377px;
  }
  .offer {
    position: absolute;
    right: 30px; top: 28px;
    width: 420px;
    text-align: right;
    color: var(--grey);
  }
  .offer-heading {
    color: var(--green);
    font-weight: 700;
    font-size: 16px;
    letter-spacing: 0.3px;
    margin-bottom: 4px;
  }
  .offer-list { list-style: none; font-size: 14px; line-height: 1.5; }
  .offer-list li::after {
    content: "";
    display: inline-block;
    width: 7px; height: 7px;
    margin-left: 8px;
    border-radius: 50%;
    background: var(--green);
    vertical-align: middle;
  }
  .offer-pitch { font-size: 14px; line-height: 1.5; }
  .special-heading {
    color: var(--green);
    font-weight: 700;
    font-size: 18px;
    margin-top: 12px;
  }
  .special-detail { color: var(--ink); font-weight: 700; font-size: 14px; }
  .company-name {
    margin-top: 12px;
    color: var(--ink);
    font-weight: 800;
    font-size: 30px;
    line-height: 1.1;
    white-space: nowrap;
  }
  .company-tagline { font-size: 12px; color: var(--grey); margin-top: 4px; }

  /* Front side */
  .logo {
    position: absolute;
    left: 44px; top: 44px;
    display: flex;
    align-items: center;
    gap: 12px;
  }
  .logo-dot {
    width: 30px; height: 30px;
    border-radius: 50%;
    background: var(--green-light);
  }
  .logo-name {
    color: var(--ink);
    font-weight: 800;
    font-size: 28px;
    line-height: 1;
    white-space: nowrap;
  }
  .logo-tagline {
    position: absolute;
    left: 86px; top: 84px;
    font-size: 12px;
    color: var(--grey);
  }
  .contact-panel {
    position: absolute;
    right: -180px; bottom: -320px;
    width: 560px; height: 560px;
    border-radius: 50%;
    background: radial-gradient(circle at 30% 25%, var(--green-light), var(--green) 55%, var(--green-deep));
  }
  .contact {
    position: absolute;
    right: 40px; bottom: 30px;
    text-align: right;
    color: var(--white);
    font-size: 16px;
    line-height: 1.45;
  }
  .contact-name { font-weight: 700; font-size: 20px; }
  .contact-title { font-size: 16px; margin-bottom: 10px; }
</style>
</head>
<body>

  <section class="card card-back">
    <svg class="brand-decoration" role="img" aria-label="Large brand mark decoration in green" viewBox="0 0 200 377" preserveAspectRatio="none">
      <defs>
        <linearGradient id="decoFill" x1="0" y1="0" x2="1" y2="1">
          <stop offset="0" stop-color="#b8df8c"/>
          <stop offset="1" stop-color="#4fa82a" stop-opacity="0.55"/>
        </linearGradient>
      </defs>
      <rect width="200" height="377" fill="url(#decoFill)" opacity="0.35"/>
    </svg>

    <div class="offer">
      <p class="offer-heading">STRUGGLING WITH YOUR FINANCES?</p>
      <ul class="offer-list">
        <li>Learn to become debt free</li>
        <li>Discover the power of cash</li>
        <li>Control your money instead of it controlling you</li>
      </ul>
      <p class="offer-pitch">Let us help you achieve a new level of financial freedom!</p>
      <p class="special-heading">SPECIAL OFFER!</p>
      <p class="special-detail">FREE 30 minute consultation</p>
      <p class="company-name">Summit Money Coaching</p>
      <p class="company-tagline">Achieve a new level of personal freedom</p>
    </div>
  </section>

  <section class="card card-front">
    <div class="logo">
      <span class="logo-dot"></span>
      <span class="logo-name">Summit Money Coaching</span>
    </div>
    <p class="logo-tagline">Achieve a new level of personal freedom</p>

    <div class="contact-panel"></div>
    <div class="contact">
      <p class="contact-name">Daniel R. Hayes</p>
      <p class="contact-title">Personal Financial Coach</p>
      <p>(205) 555-0148</p>
      <p>daniel@summitmoneycoach.com</p>
      <p>www.summitmoneycoach.com</p>
    </div>
  </section>

</body>
</html>
```